Cat-products company needs smart, yet endearing, business card

We need a business card design for a new, but up-and-running, business based in Honolulu, Hawaii. The business is Purrnest Nook Co. Our first product is the most environmentally-friendly cat grass kit ever seen on the planet. Future products, currently in the R&D phase, will include a variety of exciting cat scratchers. We also do consulting work to help apartment-dwellers make their home more cat-friendly and, in the future, plan on doing full, custom installs of structure to create high walkways for cats.

Target Market(s)

Middle-aged, apartment-dwelling, middle-class workers who own 1 or more cats and who dote on them.

Industry/Entity Type

Pet Care

Contact Information for Business Card

A striking, professional, yet warm and friendly design is what we're after.

Font styles to use
Serif
Sans Serif
Other font styles liked:
• Comfortaa

Colors

Designer to choose colors to be used in the design.

Requirements
Must have
• The company logo: (see attachment)
• The company name: Purrnest Nook Co
• The web address: www.purrnestnookco.com
• Email: support@purrnestnookco.com
• Phone: +1 (808) 571 6023
• Update (Fri Jun 30 3017 7:45pm Hawaii Time) I would like, is possible, uploaded picture of the cat grass kit on the back of the card with some text along the lines of: Purrnest Nook Co - Maker Of The Leafiest Feline Sprout Set Yet
Nice to have
• A cat picture, cartoon, real or silhouette that illustrates cats in action and/or relaxing; ie using the apartment space to live, play and relax in and being well-contented.
• Most of the website is done in the font: Comfortaa. It might be nice to continue using this for brand consistency.
Should not have
• Hard-to-read fonts.

```html
<!DOCTYPE html>
<html lang="en">
<head>
<meta charset="utf-8">
<title>Purrnest Nook Co — Business Card</title>
<link href="https://fonts.googleapis.com/css2?family=Comfortaa:wght@400;700&display=swap" rel="stylesheet">
<style>
  :root {
    --page: #ece8e3;
    --white: #ffffff;
    --paper: #f4f4f2;
    --brown: #6b3f3a;
    --brown-deep: #5a332f;
    --yellow: #f2c21b;
    --cream: #f3e2c8;
    --cream-deep: #dcc1a0;
    --text-light: #f6ece6;
  }
  html, body {
    margin: 0;
    padding: 0;
    width: 1200px;
    height: 780px;
    overflow: hidden;
    background: var(--page);
    font-family: "Comfortaa", sans-serif;
  }
  .canvas {
    position: relative;
    width: 1200px;
    height: 780px;
  }
  .card {
    position: absolute;
    top: 240px;
    width: 525px;
    height: 300px;
    overflow: hidden;
    box-shadow: 0 10px 28px rgba(60, 35, 25, 0.22);
  }
  /* Front */
  .card-front { left: 40px; background: var(--brown); }
  .front-top {
    position: absolute;
    left: 0; top: 0;
    width: 100%; height: 150px;
    background: linear-gradient(180deg, var(--white), var(--paper));
  }
  .brand-name {
    position: absolute;
    left: 34px; top: 38px;
    width: 240px;
    margin: 0;
    font-size: 34px;
    line-height: 38px;
    font-weight: 700;
    color: var(--yellow);
    letter-spacing: 0.5px;
  }
  .pet-photo {
    position: absolute;
    right: 50px; top: 0;
    width: 160px; height: 186px;
    border-radius: 0 0 36px 36px;
    background: radial-gradient(ellipse at 50% 40%, var(--cream) 0%, var(--cream-deep) 100%);
    z-index: 2;
  }
  .name-band {
    position: absolute;
    left: 0; top: 150px;
    width: 100%; height: 38px;
    background: var(--yellow);
  }
  .employee-name {
    position: absolute;
    left: 34px; top: 10px;
    margin: 0;
    font-size: 17px;
    font-weight: 700;
    color: var(--white);
  }
  .contact-list {
    position: absolute;
    left: 34px; top: 202px;
    margin: 0; padding: 0;
    list-style: none;
  }
  .contact-item {
    display: flex;
    align-items: center;
    gap: 10px;
    height: 28px;
    font-size: 13.5px;
    color: var(--text-light);
  }
  .contact-icon { width: 18px; height: 18px; flex: none; }
  /* Back */
  .card-back {
    left: 635px;
    background: radial-gradient(ellipse at 50% 40%, var(--brown) 0%, var(--brown-deep) 100%);
    display: flex;
    flex-direction: column;
    align-items: center;
    justify-content: center;
    gap: 22px;
  }
  .back-mark {
    display: flex;
    align-items: center;
    gap: 14px;
  }
  .back-mark-square {
    width: 40px; height: 40px;
    background: var(--yellow);
    flex: none;
  }
  .back-brand {
    margin: 0;
    font-size: 30px;
    font-weight: 700;
    color: var(--white);
    white-space: nowrap;
  }
  .back-web {
    margin: 0;
    font-size: 14px;
    color: var(--text-light);
  }
</style>
</head>
<body>
<main class="canvas">

  <section class="card card-front" aria-label="Business card front">
    <div class="front-top">
      <h1 class="brand-name">Purrnest<br>Nook Co</h1>
    </div>
    <div class="pet-photo" role="img" aria-label="Photo of a cream-coloured cat resting its paws over the name band"></div>
    <div class="name-band">
      <p class="employee-name">Employee Name</p>
    </div>
    <ul class="contact-list">
      <li class="contact-item">
        <svg class="contact-icon" viewBox="0 0 18 18" aria-hidden="true">
          <circle cx="9" cy="9" r="8" fill="none" stroke="#f2c21b" stroke-width="1.5"/>
          <path d="M6 5.5 L7.5 5.5 L8.2 7.4 L7.3 8.2 Q8 9.8 9.8 10.7 L10.6 9.8 L12.5 10.5 L12.5 12 Q9.5 12.6 7.4 10.6 Q5.4 8.5 6 5.5 Z" fill="#f2c21b"/>
        </svg>
        <span>+1 (808) 571 6023</span>
      </li>
      <li class="contact-item">
        <svg class="contact-icon" viewBox="0 0 18 18" aria-hidden="true">
          <circle cx="9" cy="9" r="8" fill="none" stroke="#f2c21b" stroke-width="1.5"/>
          <rect x="5" y="6" width="8" height="6" fill="none" stroke="#f2c21b" stroke-width="1.2"/>
          <path d="M5 6 L9 9.3 L13 6" fill="none" stroke="#f2c21b" stroke-width="1.2"/>
        </svg>
        <span>support@purrnestnookco.com</span>
      </li>
      <li class="contact-item">
        <svg class="contact-icon" viewBox="0 0 18 18" aria-hidden="true">
          <circle cx="9" cy="9" r="8" fill="none" stroke="#f2c21b" stroke-width="1.5"/>
          <circle cx="9" cy="9" r="4.2" fill="none" stroke="#f2c21b" stroke-width="1.1"/>
          <ellipse cx="9" cy="9" rx="1.8" ry="4.2" fill="none" stroke="#f2c21b" stroke-width="1"/>
          <line x1="4.8" y1="9" x2="13.2" y2="9" stroke="#f2c21b" stroke-width="1"/>
        </svg>
        <span>www.purrnestnookco.com</span>
      </li>
    </ul>
  </section>

  <section class="card card-back" aria-label="Business card back">
    <div class="back-mark">
      <span class="back-mark-square" aria-hidden="true"></span>
      <h2 class="back-brand">Purrnest Nook Co</h2>
    </div>
    <p class="back-web">www.purrnestnookco.com</p>
  </section>

</main>
</body>
</html>
```